Volbrey Inc Business Card

Looking to get an updated business card for a Contract Machining company (www.volbreyinc.example) - looking for a clean design the portrays the technical nature of the business - colors can follow the website design and be in any combination that makes sense (red black, white, metallic or silver) - logos attached for use also. Would like space for: Name, title, business phone (555 214-3086), cell phone , website (www.volbreyinc.example) - possibly QR code could be integrated for website (designer choice), business address - 418 Harlow Bend, Tessel Falls, ST 48199 (cards will be for 4 employees, I will either need to modify a template or I can provide individual information)
Target Market(s)
Aerospace, defense and medical device manufacturing companies that need machining
Industry/Entity Type
Machining for aerospace, defense, medical
Contact Information for Business Card
Name, Title, Business Phone, Cell Phone, email, business website and business address
Look and feel

```html
<!DOCTYPE html>
<html lang="en">
<head>
<meta charset="utf-8">
<title>Volbrey Inc Business Card</title>
<link rel="stylesheet" href="https://fonts.googleapis.com/css2?family=Montserrat:wght@400;500;800&display=swap">
<style>
  :root {
    --brand-red: #b21f25;
    --ink-black: #161616;
    --paper-white: #ffffff;
    --stage: #e6e6e6;
  }
  * { box-sizing: border-box; margin: 0; padding: 0; }
  html, body { width: 1200px; height: 900px; overflow: hidden; }
  body {
    background: var(--stage);
    font-family: "Montserrat", sans-serif;
    display: flex;
    flex-direction: column;
    align-items: center;
    justify-content: center;
    gap: 30px;
  }
  .card {
    position: relative;
    width: 700px;
    height: 400px;
    border-radius: 22px;
    overflow: hidden;
  }
  /* Front */
  .card-front {
    background: var(--brand-red);
    display: flex;
    flex-direction: column;
    align-items: center;
    justify-content: center;
    gap: 24px;
  }
  .front-disc {
    width: 180px;
    height: 180px;
    border-radius: 50%;
    background: var(--paper-white);
  }
  .front-name {
    color: var(--paper-white);
    font-weight: 800;
    font-size: 46px;
    letter-spacing: 1px;
    text-transform: uppercase;
    line-height: 1;
  }
  /* Back */
  .card-back { background: var(--ink-black); }
  .back-halo {
    position: absolute;
    left: 375px;
    top: -150px;
    width: 500px;
    height: 500px;
    border-radius: 50%;
    background: var(--paper-white);
  }
  .back-disc {
    position: absolute;
    left: 410px;
    top: -115px;
    width: 430px;
    height: 430px;
    border-radius: 50%;
    background: var(--brand-red);
  }
  .back-info {
    position: absolute;
    left: 36px;
    top: 36px;
    color: var(--paper-white);
  }
  .back-name {
    color: var(--brand-red);
    font-weight: 800;
    font-size: 44px;
    letter-spacing: 1px;
    text-transform: uppercase;
    line-height: 1;
  }
  .person {
    margin-top: 26px;
    border-left: 9px solid var(--brand-red);
    padding-left: 14px;
  }
  .person-name {
    color: var(--brand-red);
    font-weight: 800;
    font-size: 30px;
    text-transform: uppercase;
    letter-spacing: 0.5px;
    line-height: 1.1;
  }
  .person-title { font-size: 20px; font-weight: 400; margin-top: 2px; line-height: 1.3; }
  .address { margin-top: 14px; padding-left: 23px; font-size: 19px; line-height: 1.32; }
  .contacts { list-style: none; margin-top: 12px; padding-left: 23px; font-size: 18px; }
  .contacts li { display: flex; align-items: center; gap: 10px; line-height: 1.42; }
  .contacts svg { width: 16px; height: 16px; fill: var(--brand-red); flex: none; }
</style>
</head>
<body>
  <section class="card card-front" aria-label="Card front">
    <div class="front-disc"></div>
    <div class="front-name">Volbrey Inc</div>
  </section>

  <section class="card card-back" aria-label="Card back">
    <div class="back-halo"></div>
    <div class="back-disc"></div>
    <div class="back-info">
      <div class="back-name">Volbrey Inc</div>
      <div class="person">
        <div class="person-name">Dorian Fell</div>
        <div class="person-title">Managing Director</div>
      </div>
      <p class="address">418 Harlow Bend,<br>Tessel Falls, ST 48199</p>
      <ul class="contacts">
        <li><svg viewBox="0 0 24 24" aria-hidden="true"><path d="M6.6 10.8a15 15 0 0 0 6.6 6.6l2.2-2.2c.3-.3.7-.4 1-.2 1.1.4 2.3.6 3.6.6.6 0 1 .4 1 1V20c0 .6-.4 1-1 1A17 17 0 0 1 3 4c0-.6.4-1 1-1h3.5c.6 0 1 .4 1 1 0 1.3.2 2.5.6 3.6.1.3 0 .7-.2 1z"/></svg>(555 214-3086</li>
        <li><svg viewBox="0 0 24 24" aria-hidden="true"><path d="M7 1h10a2 2 0 0 1 2 2v18a2 2 0 0 1-2 2H7a2 2 0 0 1-2-2V3a2 2 0 0 1 2-2zm0 3v14h10V4zm5 15.5a1 1 0 1 0 0 2 1 1 0 0 0 0-2z"/></svg>555-673-0921</li>
        <li><svg viewBox="0 0 24 24" aria-hidden="true"><path d="M2 5h20v14H2zm2 2v.5l8 5 8-5V7zm0 2.8V17h16V9.8l-8 5z"/></svg>info@volbreyinc.example</li>
        <li><svg viewBox="0 0 24 24" aria-hidden="true"><path d="M12 2a10 10 0 1 0 0 20 10 10 0 0 0 0-20zm-1 17.9A8 8 0 0 1 4.1 11H8c.1 3.3 1.2 6.4 3 8.9zM8 9H4.1A8 8 0 0 1 11 4.1 16 16 0 0 0 8 9zm5 10.9c1.8-2.5 2.9-5.6 3-8.9h3.9a8 8 0 0 1-6.9 8.9zM10 11h4c-.1 2.7-.9 5.3-2 7.3-1.1-2-1.9-4.6-2-7.3zm0-2c.1-2.1.8-4 2-5.6 1.2 1.6 1.9 3.5 2 5.6zm6 0a16 16 0 0 0-3-4.9A8 8 0 0 1 19.9 9z"/></svg>www.volbreyinc.example</li>
      </ul>
    </div>
  </section>
</body>
</html>
```